Printing Company needs Website

PLEASE REVIEW ALL IMAGES, I HAVE INCLUDED A WEBSITE MOCKUP IDEA AND LOGO FILES IN THESE IMAGES.

Vel-Marks Provides printing services to multiple businesses. We Focus on 4 main markets. Signage (Signs, Banners, Wraps, Custom graphics), Printing (flyers, brochures, business cards, Postcards), Apparel (printed shirts, hoodies, sweatshirts), Promotional Products (mugs, golf balls, brava cans, pens), We try to sell ourselves on total brand imaging, our slogan is "Mark Everything." because we want to be able to provide any type of printing to our customers. Consumer targeting should be targeted towards small business, and wholesale targeting should be geared toward, merchandising, branding, marketing, design, signage, apparel, embroidery, and printing groups. WE DO OFFER DESIGN SERVICES, I have attached one orlwick guild logo design as an example.

I need a website designed both for wholesale and consumer based people. Wholesale customers would have their own login and consumers would also have their own.
I need there to be an online designer software (possibly java) built in so that the customer can order their product or upload their artwork online to see the proof for approval. There will need to be an commence setup, and I do have a quillpay account if that helps. Shipping must be auto calculated at the time of ordering. I would Like to make it to where when customer orders a product if it is outside of the dimensions requested on the site that the customer is warned of clipping or skewing.

I will be working closely aside the designer I pick to aid in the uploading and configuration of pricing structure, weight, and imagery if selected. This will be a lengthy project, and I will be willing to pay for the additional help so long as you are completely aware of the needs, Happy designing!!
Updates

I love all of the designs so far everyone! I will be reviewing PLEASE NOTE, IF I APPROVE YOUR WEB DESIGN, I WILL WANT YOU TO COMPLETE THE ENTIRE DESIGN INCLUDING A DESIGN PROOFING SETUP FOR MY CUSTOMERS INTEGRATED IN AS I HAVE STATED IN THE ORIGINAL STATEMENT. PLEASE ASK QUESTIONS IF YOU DON'T UNDERSTAND!

Target Market(s)

Small Business, School Athletics, Merchandising groups, Branding Groups, Larger Printers, Sign makers, Embroidery shops, Screen Printing Shops

Industry/Entity Type

It Company

Font styles to use
Sans Serif

Colors
000000
1b1b1b
757575
ec1f27

Requirements
Must have
• Built in design setup to each product with sizing, Ability to add pre-designed templates, .pdf print ready files after upload, Wholesale account, or Business accounts all with different pricing structures, Must be willing to aid in setup of all products and services (willing pay additional for setup costs.)
Nice to have
• SEO Optimization, targeting specific groups listed, automatic ordering to outsource vendors straight from site listing drop ship location if need be.

```html
<!DOCTYPE html>
<html lang="en">
<head>
<meta charset="utf-8">
<title>Vel-Marks — Mark Everything.</title>
<link href="https://fonts.googleapis.com/css2?family=Figtree:wght@400;600;700&family=Open+Sans:wght@400;600&display=swap" rel="stylesheet">
<style>
:root{
  --black:#000000;
  --charcoal:#1b1b1b;
  --grey:#757575;
  --muted:#a9a9a9;
  --red:#ec1f27;
  --red-dark:#c8161d;
  --white:#ffffff;
}
*{margin:0;padding:0;box-sizing:border-box}
html,body{width:1118px;height:1200px;overflow:hidden;background:var(--black)}
body{position:relative;font-family:"Open Sans",sans-serif;color:var(--white)}
.site-header{position:absolute;left:0;top:0;width:1118px;height:110px;background:var(--black)}
.main-nav{position:absolute;left:0;top:110px;width:1118px;height:50px;background:var(--red)}
.main-nav a{position:absolute;top:0;height:50px;line-height:50px;font-family:"Figtree",sans-serif;font-size:16px;color:var(--white);text-decoration:none;text-align:center}
.main-nav a.is-current{background:var(--red-dark)}
.main-nav .divider{position:absolute;top:0;width:1px;height:50px;background:rgba(255,255,255,.35)}
.brand-badge{position:absolute;left:487px;top:18px;width:144px;height:112px;border-radius:50%;background:var(--black);z-index:2}
.brand{position:absolute;left:420px;top:32px;width:280px;text-align:center;z-index:3}
.brand-name{font-family:"Figtree",sans-serif;font-weight:700;font-size:42px;letter-spacing:-.5px;color:var(--white);line-height:1}
.brand-tag{font-family:"Open Sans",sans-serif;font-size:12px;color:var(--white);margin-top:4px;padding-left:110px}
.brand-dot{display:inline-block;width:10px;height:10px;border-radius:50%;background:var(--red);margin-left:4px;vertical-align:top}
.hero{position:absolute;left:0;top:160px;width:1118px;height:470px;overflow:hidden}
.hero-photo{position:absolute;inset:0;background:linear-gradient(180deg,#8fb4cf 0%,#5f7f55 30%,#4d7636 60%,#3c5f29 100%)}
.hero-title{position:absolute;left:113px;top:218px;font-family:"Figtree",sans-serif;font-weight:700;font-size:48px;letter-spacing:.5px;color:var(--white);text-shadow:0 1px 3px rgba(0,0,0,.35)}
.hero-sub{position:absolute;left:113px;top:276px;font-family:"Figtree",sans-serif;font-weight:700;font-size:26px;color:var(--white);text-shadow:0 1px 3px rgba(0,0,0,.35)}
.services{position:absolute;left:0;top:630px;width:1118px;height:254px;background:var(--black)}
.service{position:absolute;top:0;width:220px;text-align:center}
.service svg{position:absolute;left:0;top:-42px}
.service-title{position:absolute;top:135px;left:0;width:100%;font-family:"Open Sans",sans-serif;font-size:20px;letter-spacing:.5px;color:var(--white)}
.service-desc{position:absolute;top:167px;left:5px;width:210px;font-size:13px;line-height:18px;color:var(--muted)}
.site-footer{position:absolute;left:0;top:884px;width:1118px;height:316px;background:var(--charcoal)}
.footer-brand{position:absolute;left:119px;top:60px}
.footer-brand .brand-name{font-size:36px}
.footer-brand .brand-tag{font-size:11px;padding-left:120px;margin-top:3px}
.footer-col{position:absolute;top:56px}
.footer-col h3{font-family:"Figtree",sans-serif;font-weight:400;font-size:17px;letter-spacing:.4px;color:var(--white);margin-bottom:14px}
.footer-col li{list-style:none;font-size:13px;line-height:27px;color:var(--white)}
.social li{display:flex;align-items:center;line-height:33px}
.social .dot{width:23px;height:23px;border-radius:50%;margin-right:10px;flex:none}
.footer-rule{position:absolute;left:112px;top:255px;width:895px;height:1px;background:#3a3a3a}
.copyright{position:absolute;left:0;top:274px;width:1102px;text-align:center;font-size:12.5px;color:var(--grey)}
</style>
</head>
<body>
<header class="site-header"></header>
<div class="brand-badge"></div>
<div class="brand">
  <div class="brand-name">Vel-Marks<span class="brand-dot"></span></div>
  <div class="brand-tag">Mark Everything.</div>
</div>
<nav class="main-nav">
  <a class="is-current" href="#" style="left:112px;width:85px">Home</a>
  <a href="#" style="left:197px;width:88px">Signage</a><span class="divider" style="left:285px"></span>
  <a href="#" style="left:286px;width:83px">Printing</a><span class="divider" style="left:369px"></span>
  <a href="#" style="left:370px;width:70px">Design</a>
  <a href="#" style="left:595px;width:112px">Promotional</a><span class="divider" style="left:707px"></span>
  <a href="#" style="left:708px;width:83px">Apparel</a><span class="divider" style="left:791px"></span>
  <a href="#" style="left:792px;width:95px">About Us</a><span class="divider" style="left:887px"></span>
  <a href="#" style="left:888px;width:111px">Contact Us</a>
</nav>

<section class="hero">
  <div class="hero-photo" role="img" aria-label="Photo of a finished outdoor monument sign on a lawn with trees and blue sky"></div>
  <h1 class="hero-title">MARK EVERYTHING</h1>
  <p class="hero-sub">MAURIS VEL LACUS VITAE</p>
</section>

<section class="services">
  <div class="service" style="left:101px">
    <svg width="220" height="176" viewBox="0 0 220 176" aria-hidden="true">
      <defs><linearGradient id="gPurple" x1="0" y1="0" x2="0" y2="1"><stop offset="0" stop-color="#b02cb8"/><stop offset="1" stop-color="#4b0d52"/></linearGradient></defs>
      <path d="M50 40 A88 88 0 0 1 205 34" fill="none" stroke="#fff" stroke-width="10"/>
      <ellipse cx="118" cy="90" rx="78" ry="74" transform="rotate(-20 118 90)" fill="none" stroke="url(#gPurple)" stroke-width="22"/>
      <ellipse cx="118" cy="90" rx="66" ry="62" fill="#000"/>
      <g fill="none" stroke="#fff" stroke-width="3.5"><line x1="90" y1="55" x2="146" y2="55"/><path d="M100 56 V114 L118 102 L136 114 V56"/><rect x="114" y="70" width="8" height="12"/></g>
    </svg>
    <div class="service-title">Signage</div>
    <div class="service-desc">Signs, Banners, Wraps, Custom graphics</div>
  </div>
  <div class="service" style="left:328px">
    <svg width="220" height="176" viewBox="0 0 220 176" aria-hidden="true">
      <defs><linearGradient id="gSky" x1="0" y1="0" x2="0" y2="1"><stop offset="0" stop-color="#bfe3f0"/><stop offset="1" stop-color="#3a9cc7"/></linearGradient></defs>
      <path d="M50 40 A88 88 0 0 1 205 34" fill="none" stroke="#fff" stroke-width="10"/>
      <ellipse cx="118" cy="90" rx="78" ry="74" transform="rotate(-20 118 90)" fill="none" stroke="url(#gSky)" stroke-width="22"/>
      <ellipse cx="118" cy="90" rx="66" ry="62" fill="#000"/>
      <g fill="none" stroke="#fff" stroke-width="3.5"><rect x="100" y="64" width="36" height="14"/><rect x="86" y="78" width="64" height="26" rx="3"/><rect x="98" y="94" width="40" height="20"/><line x1="104" y1="102" x2="132" y2="102"/><line x1="104" y1="108" x2="132" y2="108"/></g>
    </svg>
    <div class="service-title">Printing</div>
    <div class="service-desc">flyers, brochures, business cards, Postcards</div>
  </div>
  <div class="service" style="left:556px">
    <svg width="220" height="176" viewBox="0 0 220 176" aria-hidden="true">
      <defs><linearGradient id="gYellow" x1="0" y1="0" x2="0" y2="1"><stop offset="0" stop-color="#fff200"/><stop offset="1" stop-color="#ecd400"/></linearGradient></defs>
      <path d="M50 40 A88 88 0 0 1 205 34" fill="none" stroke="#fff" stroke-width="10"/>
      <ellipse cx="118" cy="90" rx="78" ry="74" transform="rotate(-20 118 90)" fill="none" stroke="url(#gYellow)" stroke-width="22"/>
      <ellipse cx="118" cy="90" rx="66" ry="62" fill="#000"/>
      <path d="M106 58 Q118 66 130 58 L150 68 L144 84 L136 80 V120 H100 V80 L92 84 L86 68 Z" fill="none" stroke="#fff" stroke-width="3"/>
    </svg>
    <div class="service-title">Apparel</div>
    <div class="service-desc" style="left:30px;width:160px">Printed shirts, hoodies, sweatshirts</div>
  </div>
  <div class="service" style="left:783px">
    <svg width="220" height="176" viewBox="0 0 220 176" aria-hidden="true">
      <defs><linearGradient id="gRed" x1="0" y1="0" x2="0" y2="1"><stop offset="0" stop-color="#f25058"/><stop offset="1" stop-color="#d90f17"/></linearGradient></defs>
      <path d="M50 40 A88 88 0 0 1 205 34" fill="none" stroke="#fff" stroke-width="10"/>
      <ellipse cx="118" cy="90" rx="78" ry="74" transform="rotate(-20 118 90)" fill="none" stroke="url(#gRed)" stroke-width="22"/>
      <ellipse cx="118" cy="90" rx="66" ry="62" fill="#000"/>
      <g fill="none" stroke="#fff" stroke-width="3"><path d="M98 66 H134 M100 66 V76 M132 66 V76"/><path d="M96 80 H136 V88 Q136 102 116 102 Q96 102 96 88 Z"/><path d="M136 84 Q148 84 144 94 Q141 99 134 98"/><path d="M86 108 H146"/><path d="M94 112 H138"/></g>
    </svg>
    <div class="service-title">Promotional Products</div>
    <div class="service-desc" style="left:0;width:220px">Mugs, golf balls, brava cans, pens</div>
  </div>
</section>

<footer class="site-footer">
  <div class="footer-brand">
    <div class="brand-name">Vel-Marks<span class="brand-dot"></span></div>
    <div class="brand-tag">Mark Everything.</div>
  </div>
  <div class="footer-col" style="left:349px">
    <h3>COMPANY</h3>
    <ul><li>Home</li><li>Signage</li><li>Printing</li><li>Design</li></ul>
  </div>
  <div class="footer-col" style="left:489px">
    <h3>SUBLINKS</h3>
    <ul><li>Promotional</li><li>Apparel</li><li>About Us</li><li>Contact Us</li></ul>
  </div>
  <div class="footer-col" style="left:638px">
    <h3>CONTACT US</h3>
    <ul><li>418 Harrow Mill Road Suite B12</li><li>Fenwick, OR 97231</li><li>(555) 301-4820</li><li>hello@velmarks.example</li></ul>
  </div>
  <div class="footer-col social" style="left:875px">
    <h3>FOLLOW US</h3>
    <ul>
      <li><span class="dot" style="background:#3b5aa0"></span>Pagebook</li>
      <li><span class="dot" style="background:#3fa9e0"></span>Chirper</li>
      <li><span class="dot" style="background:#1f6e96"></span>Linkwork</li>
      <li><span class="dot" style="background:#d2452f"></span>Searchly +</li>
    </ul>
  </div>
  <div class="footer-rule"></div>
  <p class="copyright">© 2016 Company Name&nbsp; All right reserved&nbsp; Term of Use</p>
</footer>
</body>
</html>
```